Publisher seeks book cover / Book cover for publishing house

Full cover (front, back and side of the book). 28 cm x 20 cm total (High 20 cm, width 13, side 2 cm) Front cover: Title of the author on top, centered (Mathis Delorne) Title: Counting the rivers Subtitle: Quiet engineer maritime Bottom and centered: attached logo (Velsora Editions) in white, and edited eventualy. Side: From left to right: Editor logo (only "Velsora" word, without the "Editions" word, title and author name Back cover: Left text column ) Bottom: space available for the bar coded price and 2 or 3 lines of text Right text column (approx 6.5 cm wide) Bottom of the right colum, center of the right column: same attached logo (Velsora Editions) in white, and edited eventualy, with www.velsora-example.com below the logo. Left Lateral margin of the back cover, this book should be almost 1 cm)
Colors
Designer to choose colors to be used in the design.
Look and feel
Each slider illustrates characteristics of the customer's brand and the style your logo design should communicate.

```html
<!DOCTYPE html>
<html lang="en">
<head>
<meta charset="utf-8">
<title>Counting the Rivers – Full Cover</title>
<link rel="stylesheet" href="https://fonts.googleapis.com/css2?family=Cinzel:wght@400;500&family=Open+Sans:wght@400&family=Oswald:wght@500&display=swap">
<style>
  :root {
    --page: #f4f2f3;
    --paper: #ffffff;
    --sky-top: #ffffff;
    --sky-low: #dfe6ee;
    --column-top: #2f4560;
    --column-bottom: #5d7590;
    --spine: #bfe0e2;
    --ink: #1c1c1c;
    --author: #4a2e12;
    --subtitle-grey: #3d4854;
    --brand-green: #4f6a12;
    --t-blue: #1f4fbf;
    --t-green: #2e7d32;
    --t-brown: #6b3d1e;
    --t-red: #b02020;
    --t-gold: #e0b400;
    --t-slate: #557080;
    --t-rust: #b44a24;
  }
  * { box-sizing: border-box; margin: 0; padding: 0; }
  html, body { width: 1200px; height: 806px; overflow: hidden; background: var(--page); }
  body { position: relative; font-family: "Open Sans", Arial, sans-serif; }

  .cover-sheet {
    position: absolute; left: 71px; top: 23px; width: 1061px; height: 763px;
    background: linear-gradient(180deg, var(--sky-top) 0%, var(--sky-top) 20%, var(--sky-low) 56%);
  }
  .scene-band {
    position: absolute; left: 0; top: 428px; width: 1061px; height: 335px;
    background: linear-gradient(180deg,
      rgba(223,230,238,0) 0%, #b9c6d3 14%, #6f8094 30%, #47576a 36%,
      #4fc4cf 44%, #3fd0da 56%, #b5ecef 72%, #eef6f3 86%, #ffffff 100%);
  }

  /* back cover */
  .back-column {
    position: absolute; left: 89px; top: 34px; width: 169px; height: 566px;
    background: linear-gradient(180deg, var(--column-top), var(--column-bottom));
    color: #fff; font-size: 13.2px; line-height: 18.3px; padding: 11px 4px 0 14px;
  }
  .back-column p + p { margin-top: 18px; }
  .back-note {
    position: absolute; left: 96px; top: 602px; width: 140px;
    text-align: center; font-family: Arial, sans-serif; font-size: 13.5px; line-height: 18.3px; color: #000;
  }
  .price-space { position: absolute; left: 103px; top: 693px; width: 140px; height: 71px; background: var(--paper); }
  .blurb-box {
    position: absolute; left: 282px; top: 38px; width: 273px; height: 589px;
    border: 1px solid #222; background: rgba(255,255,255,0.9);
    color: var(--ink); font-size: 13.2px; line-height: 18.3px; padding: 4px 6px 0 9px;
  }
  .blurb-box p + p { margin-top: 18px; }

  .publisher-plate {
    position: absolute; width: 110px; height: 59px; background: var(--paper);
    display: flex; align-items: center; justify-content: center; flex-direction: column;
    font-family: "Oswald", sans-serif; font-weight: 500; color: var(--brand-green);
    font-size: 15px; line-height: 18px; text-align: center;
  }
  .publisher-plate.back { left: 359px; top: 699px; }
  .publisher-plate.front { left: 826px; top: 699px; }

  /* spine */
  .spine {
    position: absolute; left: 564px; top: 23px; width: 77px; height: 763px;
    background: linear-gradient(180deg, #ffffff 0%, #ffffff 55%, var(--spine) 62%, #a9d8dc 100%);
  }
  .spine-brand {
    position: absolute; left: 0; top: 22px; width: 77px; text-align: center;
    font-family: "Oswald", sans-serif; font-weight: 500; font-size: 15px; color: var(--brand-green);
  }
  .spine-text {
    position: absolute; left: 24px; top: 78px; writing-mode: vertical-rl;
    font-family: "Cinzel", serif; white-space: nowrap;
  }
  .spine-title { font-size: 27px; letter-spacing: 0.5px; }
  .spine-title .rest { color: var(--subtitle-grey); font-size: 25px; margin-top: 14px; }
  .spine-author { font-size: 16px; color: var(--ink); margin-top: 40px; }

  /* front */
  .front-author {
    position: absolute; left: 641px; top: 55px; width: 491px; text-align: center;
    font-family: "Cinzel", serif; font-weight: 500; font-size: 38px; color: var(--author); letter-spacing: 1px;
  }
  .front-title {
    position: absolute; left: 641px; top: 160px; width: 491px; text-align: center;
    font-family: "Cinzel", serif; font-size: 78px; line-height: 1; letter-spacing: -1px;
  }
  .front-title-rest {
    position: absolute; left: 641px; top: 288px; width: 491px; text-align: center;
    font-family: "Cinzel", serif; font-size: 46px; color: var(--subtitle-grey); letter-spacing: 2px;
  }
  .front-subtitle {
    position: absolute; left: 641px; top: 367px; width: 491px; text-align: center;
    font-size: 22px; color: #2a2f36;
  }
  .c1 { color: var(--t-blue); } .c2 { color: var(--t-green); } .c3 { color: var(--t-brown); }
  .c4 { color: var(--t-red); } .c5 { color: var(--t-gold); } .c6 { color: var(--t-slate); }
  .c7 { color: var(--t-rust); } .c8 { color: var(--t-green); }
</style>
</head>
<body>
  <div class="cover-sheet">
    <div class="scene-band" role="img" aria-label="Painted view of a turquoise lagoon with a dark island and a small aircraft flying over white sand"></div>
  </div>

  <section class="back-cover">
    <div class="back-column">
      <p>Lorem ipsum dolor sit amet, consectetur adipiscing elit, sed do eiusmod tempor incididunt ut labore et dolore magna aliqua. Quis ipsum suspendisse ultrices gravida. Risus commodo viverra maecenas accumsan lacus vel facilisis.</p>
      <p>Lorem ipsum dolor sit amet, consectetur adipiscing elit, sed do eiusmod tempor incididunt ut labore et dolore magna aliqua. Quis ipsum suspendisse ultrices gravida. Risus commodo viverra maecenas accumsan lacus vel facilisis. amet, consectetur adipiscing elit, sed do e ultrices gravida. Risus commodo viverra maecenas accumsan lacus vel facilisis.</p>
    </div>
    <div class="back-note">Lorem ipsum dolor sit amet, consectetur adipiscing elit, sed</div>
    <div class="price-space"></div>

    <div class="blurb-box">
      <p>Lorem ipsum dolor sit amet, consectetur adipiscing elit, sed do eiusmod tempor incididunt ut labore et dolore magna aliqua. Quis ipsum suspendisse ultrices gravida. Risus commodo viverra maecenas accumsan lacus vel facilisis.</p>
      <p>Lorem ipsum dolor sit amet, consectetur adipiscing elit, sed do eiusmod tempor incididunt ut labore et dolore magna aliqua. Quis ipsum suspendisse ultrices gravida. Risus commodo viverra maecenas accumsan lacus vel facilisis.</p>
      <p>Lorem ipsum dolor sit amet, consectetur adipiscing elit, sed do eiusmod tempor incididunt ut labore et dolore magna aliqua. Quis ipsum suspendisse ultrices gravida. Risus commodo viverra maecenas accumsan lacus vel facilisis.</p>
      <p>Lorem ipsum dolor sit amet, consectetur adipiscing elit, sed do eiusmod tempor incididunt ut labore et dolore magna aliqua. Quis ipsum suspendisse ultrices gravida. Risus commodo viverra maecenas accumsan</p>
    </div>
    <div class="publisher-plate back">Velsora<br>Editions</div>
  </section>

  <section class="spine">
    <div class="spine-brand">VELSORA</div>
    <div class="spine-text">
      <span class="spine-title"><span class="c1">C</span><span class="c2">O</span><span class="c3">U</span><span class="c4">N</span><span class="c5">T</span><span class="c6">I</span><span class="c7">N</span><span class="c8">G</span></span>
      <span class="spine-title"><span class="rest">THE RIVERS</span></span>
      <span class="spine-author">MATHIS DELORNE</span>
    </div>
  </section>

  <section class="front-cover">
    <h2 class="front-author">MATHIS DELORNE</h2>
    <h1 class="front-title"><span class="c1">C</span><span class="c2">O</span><span class="c3">U</span><span class="c4">N</span><span class="c5">T</span><span class="c6">I</span><span class="c7">N</span><span class="c8">G</span></h1>
    <div class="front-title-rest">THE RIVERS</div>
    <div class="front-subtitle">Quiet Engineer</div>
    <div class="publisher-plate front">Velsora<br>Editions</div>
  </section>
</body>
</html>
```